Sparlo Nest residential and commercial cleaning

We need a Business card design for a new residential and commercial cleaning company based in UAE- Abu Dhabi named (SPARLO NEST)
we provide a residential cleaning service based in hourly rate (Maid Rent - Baby Setting), Also a commercial and offices cleaning.
Our logo is attached for your reference

Target Market(s)

Women who are 22 to 60 years old.

Industry/Entity Type

Residential

Requirements
Should not have
• it should not have an old-style fonts

```html
<!DOCTYPE html>
<html lang="en">
<head>
<meta charset="UTF-8">
<title>Sparlo Nest Business Card</title>
<link href="https://fonts.googleapis.com/css2?family=Open+Sans:wght@400;600;700&display=swap" rel="stylesheet">
<style>
  :root {
    --page-bg: #e9e7e4;
    --card-bg: #ffffff;
    --brand-blue: #1a6db5;
    --brand-green: #8cc63f;
    --ink: #1c1c1c;
    --faint-green: #cfe6ad;
    --band-text: #ffffff;
  }
  * { margin: 0; padding: 0; box-sizing: border-box; }
  html, body {
    width: 1200px; height: 1000px; overflow: hidden;
    background: var(--page-bg);
    font-family: "Open Sans", Arial, sans-serif;
    color: var(--ink);
  }
  .card {
    position: absolute; left: 265px; width: 665px; height: 396px;
    background: var(--card-bg);
    box-shadow: 0 4px 14px rgba(0,0,0,0.18);
    overflow: hidden;
  }
  .card-front { top: 73px; }
  .card-back { top: 533px; }

  .front-brand {
    position: absolute; inset: 0;
    display: flex; align-items: center; justify-content: center; gap: 22px;
  }
  .brand-name {
    font-weight: 700; color: var(--brand-blue); letter-spacing: -1px;
  }
  .front-brand .brand-name { font-size: 68px; }
  .brand-dot {
    width: 52px; height: 52px; border-radius: 50%;
    background: var(--brand-green);
  }

  .back-brand {
    position: absolute; left: 25px; top: 70px;
    display: flex; align-items: center; gap: 12px;
  }
  .back-brand .brand-name { font-size: 34px; }
  .back-brand .brand-dot { width: 22px; height: 22px; }

  .tagline {
    position: absolute; left: 25px; top: 180px;
    font-size: 17px; font-weight: 700;
  }
  .contact-list {
    position: absolute; left: 24px; top: 222px; list-style: none;
  }
  .contact-list li {
    display: flex; align-items: center; gap: 10px;
    font-size: 16px; height: 29.5px;
  }
  .contact-list svg { width: 14px; height: 14px; fill: var(--brand-green); flex: none; }

  .faint-mark {
    position: absolute; right: -30px; top: 70px;
    width: 300px; height: 300px; border-radius: 50%;
    border: 4px solid var(--faint-green); opacity: 0.7;
  }
  .services {
    position: absolute; left: 379px; top: 48px;
  }
  .services h2 { font-size: 17px; font-weight: 700; margin-bottom: 12px; }
  .services ul { list-style: none; }
  .services li { font-size: 16px; height: 38px; }

  .footer-band {
    position: absolute; left: 0; bottom: 0; width: 100%; height: 35px;
    background: var(--brand-blue); color: var(--band-text);
    display: flex; align-items: center; justify-content: center; gap: 30px;
    font-size: 17px; letter-spacing: 4px;
  }
  .footer-band .bullet { width: 9px; height: 9px; border-radius: 50%; background: var(--band-text); }
</style>
</head>
<body>
  <section class="card card-front">
    <div class="front-brand">
      <span class="brand-name">Sparlo Nest</span>
      <span class="brand-dot"></span>
    </div>
  </section>

  <section class="card card-back">
    <div class="faint-mark"></div>
    <div class="back-brand">
      <span class="brand-name">Sparlo Nest</span>
      <span class="brand-dot"></span>
    </div>
    <p class="tagline">Same Day Appointment Available !</p>
    <ul class="contact-list">
      <li><svg viewBox="0 0 14 14"><circle cx="7" cy="4" r="3.2"/><path d="M1 14c0-4 3-6 6-6s6 2 6 6z"/></svg>Dana Collins</li>
      <li><svg viewBox="0 0 14 14"><path d="M4 0h6a1 1 0 0 1 1 1v12a1 1 0 0 1-1 1H4a1 1 0 0 1-1-1V1a1 1 0 0 1 1-1zm0.5 2v8h5V2z"/></svg>Call / Text &nbsp;(702) 555 - 0148</li>
      <li><svg viewBox="0 0 14 14"><path d="M1 5c0-2 3-3 6-3s6 1 6 3v1.5h-3.5V5h-5v1.5H1zM3 8h8l2 5H1z"/></svg>Office (902) 555 - 0172</li>
      <li><svg viewBox="0 0 14 14"><path d="M7 0a7 7 0 1 0 0 14A7 7 0 0 0 7 0zm0 1.5c.8.8 1.5 2.6 1.6 4.7H5.4C5.5 4.1 6.2 2.3 7 1.5zM1.6 7.8h2.3c.1 1.6.5 3 1 4A5.5 5.5 0 0 1 1.6 7.8zm0-1.6A5.5 5.5 0 0 1 4.9 2.2c-.5 1-.9 2.4-1 4zm3.8 1.6h3.2C8.5 9.9 7.8 11.7 7 12.5c-.8-.8-1.5-2.6-1.6-4.7zm4.7 0h2.3a5.5 5.5 0 0 1-3.3 4c.5-1 .9-2.4 1-4zm0-1.6c-.1-1.6-.5-3-1-4a5.5 5.5 0 0 1 3.3 4z"/></svg>P.O. Box 40312 Abu Dhabi, UAE</li>
    </ul>
    <div class="services">
      <h2>Residential &amp; Commercial</h2>
      <ul>
        <li>- Baby Sitting</li>
        <li>- Maid Rent</li>
        <li>- Area Rugs</li>
        <li>- Steam Carpet Care</li>
        <li>- Upholstery</li>
        <li>- Air Duct Cleaning</li>
        <li>- Tile &nbsp;&amp; &nbsp;Grout Cleaning</li>
      </ul>
    </div>
    <div class="footer-band">
      <span class="bullet"></span>
      <span>Cleaner &nbsp;&amp; &nbsp;Healthier Indoor Environments</span>
      <span class="bullet"></span>
    </div>
  </section>
</body>
</html>
```